Tallow Reed Software

We are a software company selling endpoint visibility, access and security technology to enterprise-level IT departments.

Our technology helps organizations gain comprehensive visibility into and control over devices accessing their corporate network so they can quickly identify and address suspicious activity on the network that could lead to potential threats like data breaches.

This technology can cost organizations upwards of $1M - depending on the size of the organization. Our primary clients are Pinnacle 2,000 companies.

We want a professional, polished business card to represent our new brand.

Info fields to include on the card:
Name
Job Title
Office Phone #
Cell Phone #
Email address
Address: 4270 Vestridge Pond Blvd., Ste. 2600, Bloomington, MN 55812
Website address: www.tallowreedsoftware.example
Tagline: Discover the edge. Optimize the whole.

Logo files and color specs document are attached. Would like color scheme to coordinate with the logo.

Also looking at stationary/envelope designs in conjunction with the business card designs. Received very few designs that included the stationary.

Software

```html
<!DOCTYPE html>
<html lang="en">
<head>
<meta charset="utf-8">
<title>Tallow Reed Software — Business Card</title>
<link rel="stylesheet" href="https://fonts.googleapis.com/css2?family=Montserrat:wght@500;600&family=Open+Sans:wght@400;600&display=swap">
<style>
  :root {
    --backdrop: #3a302c;
    --card: #f6f6f5;
    --brand-red: #7e1d1f;
    --ink: #1f1f1f;
    --ink-soft: #4a4a4a;
    --dot-tone: rgba(150, 150, 150, 0.55);
    --dot-tone-soft: rgba(190, 190, 190, 0.35);
    --dot-fade: rgba(246, 246, 245, 0);
  }
  * { margin: 0; padding: 0; box-sizing: border-box; }
  html, body { width: 1200px; height: 768px; overflow: hidden; }
  body {
    background: var(--backdrop);
    font-family: "Open Sans", Arial, sans-serif;
    position: relative;
  }
  .card {
    position: absolute;
    width: 520px;
    height: 298px;
    background: var(--card);
    overflow: hidden;
  }
  .card--front { left: 50px; top: 235px; }
  .card--back  { left: 630px; top: 235px; }

  .brand {
    position: absolute;
    display: flex;
    align-items: center;
    gap: 10px;
    font-family: "Montserrat", Arial, sans-serif;
    font-weight: 600;
    color: var(--brand-red);
    text-transform: uppercase;
    line-height: 1.05;
    z-index: 1;
  }
  .brand__mark {
    width: 14px; height: 14px;
    background: var(--brand-red);
    flex-shrink: 0;
  }
  .brand__name span { display: block; }
  .brand__name .brand__line-top { letter-spacing: 2px; }
  .brand__name .brand__line-bottom { letter-spacing: 7px; font-size: 0.62em; }

  .card--front .brand { left: 70px; top: 70px; font-size: 28px; }
  .card--back .brand  { left: 36px; top: 32px; font-size: 20px; }

  .dot-field {
    position: absolute;
    right: 0;
  }
  .card--front .dot-field {
    bottom: 0;
    width: 270px;
    height: 250px;
    background: radial-gradient(ellipse 250px 230px at 100% 85%,
      var(--dot-tone) 0%, var(--dot-tone-soft) 45%, var(--dot-fade) 100%);
  }
  .card--back .dot-field {
    bottom: 14px;
    width: 240px;
    height: 128px;
    background: radial-gradient(ellipse 220px 120px at 100% 100%,
      var(--dot-tone) 0%, var(--dot-tone-soft) 45%, var(--dot-fade) 100%);
  }

  .contact {
    position: absolute;
    left: 36px;
    top: 112px;
    color: var(--ink);
    z-index: 1;
  }
  .contact__name { font-weight: 600; font-size: 15px; }
  .contact__title { font-size: 10.5px; color: var(--ink-soft); margin-top: 1px; }
  .contact__address { font-size: 10.5px; color: var(--ink-soft); margin-top: 16px; line-height: 1.4; }
  .contact__list { list-style: none; margin-top: 6px; font-size: 11.5px; color: var(--ink-soft); }
  .contact__list li { display: flex; align-items: center; gap: 7px; line-height: 1.55; }
  .contact__list svg { width: 10px; height: 10px; fill: var(--brand-red); }

  .website {
    position: absolute;
    right: 36px;
    top: 132px;
    font-size: 12px;
    color: var(--ink-soft);
    z-index: 1;
  }
  .band {
    position: absolute;
    left: 0; right: 0; bottom: 0;
    height: 14px;
    background: var(--brand-red);
  }
</style>
</head>
<body>

<section class="card card--front" aria-label="Business card front">
  <div class="dot-field" role="img" aria-label="Decorative field of grey dots"></div>
  <div class="brand">
    <div class="brand__mark"></div>
    <div class="brand__name">
      <span class="brand__line-top">Tallow Reed</span>
      <span class="brand__line-bottom">Software</span>
    </div>
  </div>
</section>

<section class="card card--back" aria-label="Business card back">
  <div class="dot-field" role="img" aria-label="Decorative field of grey dots"></div>
  <div class="brand">
    <div class="brand__mark"></div>
    <div class="brand__name">
      <span class="brand__line-top">Tallow Reed</span>
      <span class="brand__line-bottom">Software</span>
    </div>
  </div>

  <div class="contact">
    <p class="contact__name">Your Long Name</p>
    <p class="contact__title">Managing Director</p>
    <p class="contact__address">4270 Vestridge Pond Blvd.<br>Ste. 2600, Bloomington, MN 55812</p>
    <ul class="contact__list">
      <li>
        <svg viewBox="0 0 10 10" aria-hidden="true"><rect x="2" y="0" width="6" height="10" rx="1"/><rect x="3" y="1.2" width="4" height="6.5" fill="#f6f6f5"/></svg>
        00.123.123.123
      </li>
      <li>
        <svg viewBox="0 0 10 10" aria-hidden="true"><path d="M0 3 Q5 -1 10 3 L8.5 4.5 L7 3.5 L3 3.5 L1.5 4.5 Z"/><rect x="2" y="5" width="6" height="4.5" rx="0.6"/></svg>
        00.00.00.0000
      </li>
      <li>
        <svg viewBox="0 0 10 10" aria-hidden="true"><rect x="0" y="2" width="10" height="6.5"/><path d="M0.5 2.5 L5 6 L9.5 2.5" fill="none" stroke="#f6f6f5" stroke-width="0.9"/></svg>
        yourname@tallowreedsoftware.example
      </li>
    </ul>
  </div>

  <p class="website">www.tallowreedsoftware.example</p>
  <div class="band"></div>
</section>

</body>
</html>
```